Business Card - Tidal Lanes

Need Business Card design for company named Tidal Lanes. Software development focused mainly on Brindle Orvix & Zelt Apps. I've attached our logo with both a black and white background. Please add trademark symbol to logo when using.

```html
<!DOCTYPE html>
<html lang="en">
<head>
<meta charset="utf-8">
<title>Tidal Lanes — Business Card</title>
<link rel="stylesheet" href="https://fonts.googleapis.com/css2?family=Open+Sans:wght@400;600;700&display=swap">
<style>
  :root {
    --page-bg: #e9e4dc;
    --card-black: #050505;
    --brand-yellow: #f5b400;
    --band-olive: #5e4a06;
    --band-brown: #5a3510;
    --text-white: #ffffff;
    --text-soft: #d9d9d9;
  }
  * { box-sizing: border-box; margin: 0; padding: 0; }
  html, body {
    width: 1200px; height: 720px; overflow: hidden;
    background: var(--page-bg);
    font-family: "Open Sans", Arial, sans-serif;
  }
  .canvas { position: relative; width: 1200px; height: 720px; }
  .card {
    position: absolute; top: 205px;
    width: 540px; height: 310px;
    background: var(--card-black);
    border-radius: 4px;
    box-shadow: 0 6px 18px rgba(0,0,0,0.18);
    overflow: hidden;
  }
  .card--front { left: 40px; }
  .card--back { left: 620px; }

  /* front */
  .front-frame { position: absolute; left: 0; top: 0; }
  .wordmark {
    display: flex; align-items: center; gap: 10px;
    color: var(--text-white); font-weight: 700; letter-spacing: -0.5px;
    white-space: nowrap;
  }
  .wordmark sup { font-size: 0.35em; font-weight: 700; vertical-align: super; margin-left: 2px; }
  .wordmark__dot { width: 14px; height: 14px; border-radius: 50%; background: var(--brand-yellow); flex: none; }
  .card--front .wordmark { position: absolute; left: 34px; top: 128px; font-size: 32px; }

  .contact { position: absolute; left: 322px; top: 44px; color: var(--text-white); }
  .contact__name { color: var(--brand-yellow); font-weight: 700; font-size: 15px; line-height: 1.2; }
  .contact__title { font-size: 12px; color: var(--text-soft); margin-bottom: 14px; }
  .contact__row { display: flex; align-items: center; gap: 8px; font-size: 13px; line-height: 22px; }
  .contact__icon { width: 12px; height: 12px; flex: none; }
  .contact__address { font-size: 13px; line-height: 18px; margin-top: 16px; }

  /* back */
  .card--back .wordmark {
    position: absolute; left: 0; right: 0; top: 122px;
    justify-content: center; font-size: 52px;
  }
  .card--back .wordmark__dot { width: 20px; height: 20px; }
  .web { position: absolute; left: 0; right: 0; bottom: 28px; text-align: center; color: var(--text-soft); font-size: 12px; letter-spacing: 0.5px; }
</style>
</head>
<body>
<main class="canvas">

  <section class="card card--front" aria-label="Card front">
    <svg class="front-frame" width="540" height="310" viewBox="0 0 540 310" aria-hidden="true">
      <defs>
        <linearGradient id="bandTone" x1="0" y1="0" x2="1" y2="0">
          <stop offset="0" stop-color="var(--band-olive)" stop-opacity="1"/>
          <stop offset="1" stop-color="var(--band-brown)"/>
        </linearGradient>
      </defs>
      <path d="M284 310 V34 Q284 10 308 10 H540" fill="none" stroke="url(#bandTone)" stroke-width="12"/>
    </svg>

    <div class="wordmark"><span class="wordmark__dot"></span><span>Tidal Lanes<sup>™</sup></span></div>

    <div class="contact">
      <p class="contact__name">Your Name</p>
      <p class="contact__title">Title</p>
      <p class="contact__row">
        <svg class="contact__icon" viewBox="0 0 12 12" aria-hidden="true"><rect x="3" y="0.5" width="6" height="11" rx="1.2" fill="var(--brand-yellow)"/><rect x="4" y="2" width="4" height="5" fill="var(--card-black)"/></svg>
        555-214-7730
      </p>
      <p class="contact__row">
        <svg class="contact__icon" viewBox="0 0 12 12" aria-hidden="true"><path d="M1 8 L2.5 4.5 H9.5 L11 8 V10 H1 Z" fill="var(--brand-yellow)"/><circle cx="3.5" cy="10" r="1.2" fill="var(--card-black)"/><circle cx="8.5" cy="10" r="1.2" fill="var(--card-black)"/></svg>
        555-308-4416
      </p>
      <p class="contact__address">2290 Harbor Row<br>Marlow, FL 30417</p>
    </div>
  </section>

  <section class="card card--back" aria-label="Card back">
    <div class="wordmark"><span class="wordmark__dot"></span><span>Tidal Lanes<sup>™</sup></span></div>
    <p class="web">www.tidallanes.com</p>
  </section>

</main>
</body>
</html>
```